Re-Design an adult education portal

I need support to re-design an adult education portal. Currently the customer has an incomplete website which should be prepared in a new format.
I have the idea how to realize, but I have no clue how to design it. The hard thing is to have a "beautiful" website with available logo and main color. I hope you can support me.

Name of Website: moluvo (moluvo.ch)
Content: adult eduction for adult in safety at work, mountain climbing, dog school. various courses in different areas. But on old webpage is hard to find the different possibilities.
main color: Ral 6011 (green) -> #6C7C59
logo: you see on top of website the logo (2 dogs and a mountain with a colour gradient).

new website: for new webpage I decided to have a navigation for each section of education. In the main area I would like to have some pictures to give an idea what content is behind. At the moment it looks terrible, so I decided to use you as support for me to make the webpage prettier :). And maybe you have an better idea how to make it great. -> current state of new web page: https://moluvo.perch-net.ch/

Target Market(s)

adult eduction for adult in safety at work, mountain climbing, dog school

Number of Pages Required

1 page

Font styles to use
Serif
Sans Serif

Requirements
Must have
• As main color is set "Ral 6011" (green) -> #6C7C59

```html
<!DOCTYPE html>
<html lang="en">
<head>
<meta charset="utf-8">
<title>moluvo – Adult Education</title>
<link href="https://fonts.googleapis.com/css2?family=Jost:wght@300;400;500;600&display=swap" rel="stylesheet">
<style>
:root{
  --green:#6C7C59;
  --green-dark:#5d6c4c;
  --text:#444;
  --muted:#666;
  --light:#f4f4f4;
  --white:#fff;
}
*{margin:0;padding:0;box-sizing:border-box}
html,body{width:1200px;height:3666px;overflow:hidden}
body{font-family:'Jost',sans-serif;color:var(--text);background:var(--white);position:relative}
.abs{position:absolute}
a{color:inherit;text-decoration:none}
.btn{position:absolute;background:var(--green);color:#fff;font-size:9px;font-weight:500;letter-spacing:.4px;text-transform:uppercase;display:flex;align-items:center;justify-content:center}
.eyebrow{font-size:11px;text-transform:uppercase;color:#333;letter-spacing:.2px}
.h-green{color:var(--green);font-weight:500}
.body-copy{font-size:12.5px;line-height:24px;color:var(--muted);font-weight:300}

/* top bar */
.topbar{top:0;left:0;width:1200px;height:22px;background:var(--green);color:#fff;font-size:9px;text-transform:uppercase}
.topbar span{position:absolute;left:161px;top:5px;font-weight:300}
.topbar .social{position:absolute;right:162px;top:3px;display:flex;gap:4px}
.topbar .social i{width:16px;height:16px;border-radius:50%;background:#fff;display:block}

/* nav */
.nav{top:22px;left:0;width:1200px;height:68px;background:#fff;font-size:10.5px;color:#222}
.nav .item{position:absolute;top:27px;display:flex;align-items:center;gap:5px}
.nav .item svg{width:7px;height:5px}
.nav .active{color:var(--green)}
.brand{display:flex;align-items:center;gap:6px;font-size:22px;font-weight:500;color:var(--green)}
.brand i{width:14px;height:14px;border-radius:50%;background:var(--green);display:block}
.nav .brand{position:absolute;left:548px;top:20px}

/* hero */
.hero{top:90px;left:0;width:1200px;height:522px}
.hero .photo{position:absolute;inset:0;background:linear-gradient(160deg,#7e8a95 0%,#a9b3bb 40%,#cfd5da 70%,#b7bfc6 100%);clip-path:polygon(0 0,100% 0,100% 100%,0 90.4%)}
.hero .kicker{position:absolute;left:464px;top:152px;color:#fff;font-size:11px;font-weight:300;text-transform:uppercase}
.hero h1{position:absolute;left:464px;top:178px;width:520px;color:#fff;font-size:34px;line-height:45px;font-weight:300}
.hero h1 b{font-weight:500;color:#111}
.hero .btn{left:464px;top:340px;width:151px;height:34px}
.hero .arrow{position:absolute;top:213px;width:26px;height:46px}

/* mission */
.mission .eyebrow{position:absolute;left:161px;top:682px}
.mission h2{position:absolute;left:161px;top:702px;width:900px;font-size:28px;line-height:38px}
.mission .col{position:absolute;top:804px;width:425px}

/* about */
.about{top:1105px;left:0;width:1200px;height:548px;background:var(--light)}
.about .photo{position:absolute;left:635px;top:0;width:565px;height:548px;background:linear-gradient(180deg,#9aa3ad 0%,#d9dde0 45%,#6b6e6c 80%,#4a4542 100%)}
.about .eyebrow{position:absolute;left:71px;top:65px}
.about h2{position:absolute;left:71px;top:84px;width:540px;font-size:28px;line-height:38px}
.about .p1{position:absolute;left:71px;top:180px;width:530px}
.about .p2{position:absolute;left:71px;top:320px;width:530px}

/* courses */
.center{position:absolute;left:0;width:1200px;text-align:center}
.section-title{font-size:28px}
.sub{font-size:12.5px;line-height:23px;color:var(--muted);font-weight:300}
.card{position:absolute;width:273px;height:272px;border-radius:6px;overflow:hidden;display:flex;align-items:center;justify-content:center;flex-direction:column;color:#fff;font-size:17px;font-weight:500;text-align:center}
.card.feature{background:var(--green);font-weight:400;font-size:16px;line-height:24px;padding:0 28px}
.card.feature .ghost{margin-top:28px;width:120px;height:34px;border:1px solid #3f4a33;font-size:9px;text-transform:uppercase;display:flex;align-items:center;justify-content:center;color:#e9ede4}

/* news */
.news{top:2670px;left:0;width:1200px;height:618px;background:var(--light)}
.post{position:absolute;top:2911px;width:273px;height:295px;background:#fff;text-align:center}
.post .thumb{height:142px;background:linear-gradient(180deg,#e5e2dc 0%,#b8b2a7 50%,#5a4a3c 100%)}
.post h3{font-size:12.5px;font-weight:500;color:var(--green);margin-top:12px}
.post .meta{font-size:9.5px;color:#555;margin-top:6px;display:flex;justify-content:center;gap:16px}
.post .meta span{display:flex;align-items:center;gap:5px}
.post p{font-size:9px;line-height:13.5px;color:#444;padding:0 30px;margin-top:7px}
.post .btn{left:92px;top:256px;width:90px;height:27px;font-size:8px}

/* footer */
.footer h4{position:absolute;top:3404px;font-size:13.5px;font-weight:500;color:var(--green);text-transform:uppercase}
.footer ul{position:absolute;top:3438px;list-style:none;font-size:10.5px;color:#333}
.footer li{height:24px;display:flex;align-items:center;gap:8px}
.footer li svg{width:12px;height:12px}
.footer .about-text{position:absolute;left:843px;top:3438px;width:196px;font-size:10.5px;line-height:18px;text-align:justify;color:#333}
.footer .circles{position:absolute;left:843px;top:3558px;display:flex;gap:6px}
.footer .circles i{width:30px;height:30px;border-radius:50%;border:1.5px solid var(--green);display:block}
.bottombar{top:3624px;left:0;width:1200px;height:42px;background:var(--green);color:#fff;font-size:9.5px;display:flex;align-items:center;justify-content:center}
</style>
</head>
<body>

<div class="abs topbar"><span>Are you interested in life coaching</span><div class="social"><i></i><i></i><i></i><i></i></div></div>

<nav class="abs nav">
  <a class="item active" style="left:161px">Home</a>
  <a class="item" style="left:214px">Occupational safety <svg viewBox="0 0 7 5"><path d="M.5 .5 3.5 4 6.5 .5" fill="none" stroke="#222"/></svg></a>
  <a class="item" style="left:342px">First Aid <svg viewBox="0 0 7 5"><path d="M.5 .5 3.5 4 6.5 .5" fill="none" stroke="#222"/></svg></a>
  <a class="item" style="left:419px">Dog School <svg viewBox="0 0 7 5"><path d="M.5 .5 3.5 4 6.5 .5" fill="none" stroke="#222"/></svg></a>
  <div class="brand"><i></i>moluvo.ch</div>
  <a class="item" style="left:722px">CZV <svg viewBox="0 0 7 5"><path d="M.5 .5 3.5 4 6.5 .5" fill="none" stroke="#222"/></svg></a>
  <a class="item" style="left:781px">Mountain Training <svg viewBox="0 0 7 5"><path d="M.5 .5 3.5 4 6.5 .5" fill="none" stroke="#222"/></svg></a>
  <a class="item" style="left:902px">About moluvo <svg viewBox="0 0 7 5"><path d="M.5 .5 3.5 4 6.5 .5" fill="none" stroke="#222"/></svg></a>
</nav>

<section class="abs hero">
  <div class="photo" role="img" aria-label="Statue of a child on a tall ladder reaching into a cloudy sky"></div>
  <p class="kicker">Your training and course partner</p>
  <h1>We offer <b>training tailored</b> to your <b>needs,</b> target-oriented and tailored to <b>your skills</b> and knowledge.</h1>
  <a class="btn">Learn course now!</a>
  <svg class="arrow" style="left:32px" viewBox="0 0 26 46"><path d="M24 2 3 23l21 21" fill="none" stroke="#111" stroke-width="2.5"/></svg>
  <svg class="arrow" style="left:1136px" viewBox="0 0 26 46"><path d="M2 2l21 21L2 44" fill="none" stroke="#111" stroke-width="2.5"/></svg>
</section>

<section class="mission">
  <p class="eyebrow">Our mission &amp; vision</p>
  <h2 class="h-green">Lorem ipsum dolor sit amet, consectetur adipiscing. Etiam sollicitudin ante in purus viverra, vitae tempor lorem laoreet.</h2>
  <p class="col body-copy" style="left:161px">Lorem ipsum dolor sit amet, consectetur adipiscing elit. Etiam sollicitudin ante in purus viverra, vitae tempor lorem laoreet. Vestibulum feugiat, ipsum a euismod finibus, massa nisl tristique lacus, eget pellentesque urna metus a turpis. Nullam eget feugiat enim. Sed id finibus felis. Quisque tincidunt nisl vel risus dapibus, sit amet aliquet justo elementum. Nam non lectus nisi. Nullam eget risus neque.</p>
  <p class="col body-copy" style="left:615px">Lorem ipsum dolor sit amet, consectetur adipiscing elit. Etiam sollicitudin ante in purus viverra, vitae tempor lorem laoreet. Vestibulum feugiat, ipsum a euismod finibus, massa nisl tristique lacus, eget pellentesque urna metus a turpis. Nullam eget feugiat enim. Sed id finibus felis. Quisque tincidunt nisl vel risus dapibus, sit amet aliquet justo elementum. Nam non lectus nisi.</p>
  <a class="btn" style="left:541px;top:969px;width:118px;height:35px">Read more</a>
</section>

<section class="abs about">
  <p class="eyebrow">About us</p>
  <h2 class="h-green">Lorem ipsum dolor sit amet, consectetur adipiscing elit. tempor lorem laoreet.</h2>
  <p class="p1 body-copy">Lorem ipsum dolor sit amet, consectetur adipiscing elit. Etiam sollicitudin ante in purus viverra, vitae tempor lorem laoreet. Vestibulum feugiat, ipsum a euismod finibus, massa nisl tristique lacus, eget pellentesque urna metus a turpis. Nullam eget feugiat enim. Sed id finibus felis. Quisque tincidunt nisl vel risus dapibus, sit amet aliquet justo elementum. Nam non lectus nisi. Nullam eget risus neque.</p>
  <p class="p2 body-copy">Lorem ipsum dolor sit amet, consectetur adipiscing elit. Etiam sollicitudin ante in purus viverra, vitae tempor lorem laoreet. Vestibulum feugiat, ipsum a euismod finibus, massa nisl tristique lacus, eget pellentesque urna metus a turpis.</p>
  <a class="btn" style="left:71px;top:428px;width:118px;height:34px">Read more</a>
  <div class="photo" role="img" aria-label="Hiker with a camera standing on a rock above snowy mountain slopes"></div>
</section>

<section class="courses">
  <p class="center eyebrow" style="top:1760px">Our courses</p>
  <h2 class="center section-title h-green" style="top:1778px">Explore How can We help you</h2>
  <p class="center sub" style="top:1825px">Lorem ipsum dolor sit amet, consectetur adipiscing elit. Etiam<br>sollicitudin ante in purus viverra, vitae tempor lorem laoreet.</p>

  <div class="card" style="left:161px;top:1913px;background:linear-gradient(90deg,#4b3a36,#7b2a2a 40%,#8d8f8f)" role="img" aria-label="Worker operating a red forklift">Forklift Courses</div>
  <div class="card feature" style="left:464px;top:1913px">Personal protective equipment against falls from a height (PPE)<div class="ghost">Start here</div></div>
  <div class="card" style="left:766px;top:1913px;background:linear-gradient(180deg,#59646f,#6d6553 55%,#4a4740)" role="img" aria-label="Aerial work platform raised beside a building">Aerial work Platform</div>
  <div class="card" style="left:161px;top:2214px;background:linear-gradient(180deg,#3c3a30,#4d4a3a 50%,#556a33)" role="img" aria-label="Two dogs sitting in green grass">Dog School</div>
  <div class="card" style="left:464px;top:2214px;background:linear-gradient(180deg,#8aa3b3,#a89a8e 60%,#7f7468)" role="img" aria-label="Group practising first aid on training mannequins">First Aiders</div>
  <div class="card" style="left:766px;top:2214px;background:#8a8a8a" role="img" aria-label="Medical training partner emblem">Medical Training</div>

  <a class="btn" style="left:534px;top:2554px;width:134px;height:35px">View all courses</a>
</section>

<section class="abs news"></section>
<p class="center eyebrow" style="top:2756px">News</p>
<h2 class="center section-title h-green" style="top:2774px">Our Latest News</h2>
<p class="center sub" style="top:2822px">Lorem ipsum dolor sit amet, consectetur adipiscing elit. Etiam<br>sollicitudin ante in purus viverra, vitae tempor lorem laoreet.</p>

<article class="post" style="left:161px">
  <div class="thumb" role="img" aria-label="Hands holding glasses over a desk with coffee and a phone"></div>
  <h3>Lorem ipsum dolor sit amet, consectetur.</h3>
  <div class="meta"><span><svg width="11" height="11" viewBox="0 0 11 11"><rect x=".5" y="1.5" width="10" height="9" fill="none" stroke="#333"/><path d="M.5 4h10" stroke="#333"/></svg>May 18, 2021</span><span><svg width="11" height="10" viewBox="0 0 11 10"><path d="M.5.5h10v6.5H4L1.5 9.5V7H.5z" fill="none" stroke="#333"/></svg>12 comments</span></div>
  <p>Lorem ipsum dolor sit amet, consectetur adipiscing elit. Etiam sollicitudin ante in purus viverra, vitae tempor lorem laoreet.</p>
  <a class="btn">Read more</a>
</article>
<article class="post" style="left:464px">
  <div class="thumb" role="img" aria-label="Hands holding glasses over a desk with coffee and a phone"></div>
  <h3>Lorem ipsum dolor sit amet, consectetur.</h3>
  <div class="meta"><span><svg width="11" height="11" viewBox="0 0 11 11"><rect x=".5" y="1.5" width="10" height="9" fill="none" stroke="#333"/><path d="M.5 4h10" stroke="#333"/></svg>May 18, 2021</span><span><svg width="11" height="10" viewBox="0 0 11 10"><path d="M.5.5h10v6.5H4L1.5 9.5V7H.5z" fill="none" stroke="#333"/></svg>12 comments</span></div>
  <p>Lorem ipsum dolor sit amet, consectetur adipiscing elit. Etiam sollicitudin ante in purus viverra, vitae tempor lorem laoreet.</p>
  <a class="btn">Read more</a>
</article>
<article class="post" style="left:766px">
  <div class="thumb" role="img" aria-label="Hands holding glasses over a desk with coffee and a phone"></div>
  <h3>Lorem ipsum dolor sit amet, consectetur.</h3>
  <div class="meta"><span><svg width="11" height="11" viewBox="0 0 11 11"><rect x=".5" y="1.5" width="10" height="9" fill="none" stroke="#333"/><path d="M.5 4h10" stroke="#333"/></svg>May 18, 2021</span><span><svg width="11" height="10" viewBox="0 0 11 10"><path d="M.5.5h10v6.5H4L1.5 9.5V7H.5z" fill="none" stroke="#333"/></svg>12 comments</span></div>
  <p>Lorem ipsum dolor sit amet, consectetur adipiscing elit. Etiam sollicitudin ante in purus viverra, vitae tempor lorem laoreet.</p>
  <a class="btn">Read more</a>
</article>

<footer class="footer">
  <div class="brand abs" style="left:548px;top:3336px"><i></i>moluvo.ch</div>
  <h4 style="left:161px">Quick Links</h4>
  <ul style="left:161px"><li>Home</li><li>About moluvo</li><li>Courses</li><li>Unlock Your Potential</li><li>Contact</li></ul>
  <h4 style="left:335px">Address</h4>
  <ul style="left:335px">
    <li><svg viewBox="0 0 12 12"><path d="M6 11.5S2 7 2 4.5a4 4 0 0 1 8 0C10 7 6 11.5 6 11.5z" fill="none" stroke="#333"/><circle cx="6" cy="4.5" r="1.4" fill="none" stroke="#333"/></svg>Lindenweg 27, CH-3900 Brig</li>
    <li><svg viewBox="0 0 12 12"><rect x=".5" y="2.5" width="11" height="7" fill="none" stroke="#333"/><path d="M.5 2.5 6 7l5.5-4.5" fill="none" stroke="#333"/></svg>info@moluvo.ch</li>
    <li><svg viewBox="0 0 12 12"><rect x="3" y=".5" width="6" height="11" rx="1" fill="none" stroke="#333"/><path d="M5 9.5h2" stroke="#333"/></svg>+41 79 512 48 30</li>
  </ul>
  <h4 style="left:642px">Company</h4>
  <ul style="left:642px"><li>Home</li><li>Terms &amp; Conditions</li><li>Courses</li><li>Online Support</li><li>Contact</li></ul>
  <h4 style="left:843px">Get Connect</h4>
  <p class="about-text">Lorem ipsum dolor sit amet, consectetur adipiscing elit. Etiam sollicitudin ante in purus viverra, vitae tempor lorem laoreet. Vestibulum feugiat, ipsum a euismod finibus, massa nisl tristique lacus, eget pellentesque urna metus a turpis.</p>
  <div class="circles"><i></i><i></i><i></i><i></i></div>
</footer>

<div class="abs bottombar">© 2021 MOLUVO ALL RIGHTS RESERVED</div>

</body>
</html>
```